Brightcoat Painting Services Requires a New Responsive Site

Hi Designers,

Our current website is this www.brightcoatpainting.com.au for some idea.
I made it on Adobe Muse, its very basic.
I would like it to be redesigned to look more professional and also responsive. I actually know how to do html5 and css but I think others will do this much better than me.

I do not need content because I am a copywriter and would like to do all SEO and copy myself.

The most improtant things to remember is that the site cannot use a CMS
and the code needs to be understandable so that I can go in and add content later on and do SEO work.

Also the site requires an additional testimonial page. I would imagine a nice gallery would be a great addition too(something that I can add images too through html. Also in it is important for it to contain those brand images on the front page as it increases authority. I will attach them onto the brief.

Those two files of nearbyfind and tradeleafs are local directories where we have reviews so a placement of those on the testimonail page would make great sense. I will to the href myself.

Anyway, good luck!

I look forward to see your designs :D
Updates

I have just been informed that on this site websites are simply designed and not built (developed) if this is the case please stop working on your designs and spending more time on this project. I REQUIRE DEVELOPMENT ALSO AND HAVE ALREADY CONTACTED SUPPORT.

Target Market(s)

The target market is 30-75 high income earners.

Industry/Entity Type

Painting

Number of Pages Required

5+ page

Font styles to use
Serif
Sans Serif

Requirements
Must have
• attractive gallery, and the brand icons uploaded.
• must be responsive
• web carousel (with the different types of work we do). eg domestic, commercial, industrial etc.
Nice to have
• a little interactivity
• corporate a natural design that goes well with our logo
Should not have
• any content. just write jiberish to fill in the spaces.
• I will be doing all copy and SEO myself.
• More than five pages, bascially the four that already exist plus the testimonail one.

```html
<!DOCTYPE html>
<html lang="en">
<head>
<meta charset="utf-8">
<title>Brightcoat Painting Services</title>
<link href="https://fonts.googleapis.com/css2?family=Questrial&display=swap" rel="stylesheet">
<style>
:root{
  --brand:#1d6c9e;
  --brand-dark:#2a5d82;
  --ink:#333;
  --muted:#6c6c6c;
  --header-bg:#efefef;
  --band:#ececec;
  --footer:#4a4a4a;
  --footer-text:#bdbdbd;
  --bottom:#3c3c3c;
  --tweet:#5fa8d6;
}
*{margin:0;padding:0;box-sizing:border-box}
html,body{width:683px;height:1200px;overflow:hidden}
body{font-family:"Questrial",sans-serif;color:var(--ink);background:#fff;position:relative}
.abs{position:absolute}
.site-header{left:0;top:0;width:683px;height:78px;background:var(--header-bg);border-top:3px solid var(--brand-dark)}
.logo{left:80px;top:24px;display:flex;align-items:center;gap:6px;font-size:15px;color:var(--brand)}
.logo-square{width:14px;height:14px;background:var(--brand)}
.nav{left:256px;top:39px;font-size:7.5px;letter-spacing:.2px}
.nav a{color:#333;text-decoration:none;position:absolute;white-space:nowrap}
.nav a.active{color:var(--brand)}
.nav a.active::after{content:"";position:absolute;left:50%;top:12px;margin-left:-3px;border:3px solid transparent;border-bottom:4px solid var(--brand);border-top:0}
.hero{left:0;top:78px;width:683px;height:261px;background:linear-gradient(100deg,#6d6a5a 0%,#8a3b30 28%,#a6463a 55%,#7a2f29 80%,#5a2420 100%)}
.hero-title{right:81px;top:64px;color:#fff;font-size:29px;white-space:nowrap}
.hero-sub{right:81px;top:110px;color:#fff;font-size:13px;text-align:right;line-height:17px}
.dots{right:85px;top:162px;display:flex;gap:5px}
.dots span{width:8px;height:8px;border-radius:50%;background:#1b1b1b}
.dots span.on{background:var(--brand)}
.quality{left:0;top:339px;width:683px;height:275px;background:#fbfbfb}
.section-title{width:683px;text-align:center;font-size:14.5px;font-weight:400;color:var(--brand-dark)}
.divider{left:260px;width:163px;height:10px}
.intro{left:80px;top:60px;width:523px;text-align:center;font-size:7.3px;color:var(--muted);line-height:12px}
.service{width:130px;text-align:center}
.service .badge{width:78px;height:78px;margin:0 auto;border-radius:50%;background:var(--brand);border:3px solid #fff;box-shadow:0 2px 5px rgba(0,0,0,.25);display:flex;align-items:center;justify-content:center}
.service h3{font-weight:400;font-size:9.5px;color:var(--brand);margin-top:22px}
.service p{font-size:6.2px;color:var(--muted);line-height:11px;margin-top:2px;padding:0 10px}
.gallery{left:0;top:614px;width:683px;height:286px;background:var(--band)}
.photo{width:164px;height:101px}
.partners{left:0;top:900px;width:683px;height:96px;background:#fafafa}
.partner{width:44px;height:44px}
.site-footer{left:0;top:996px;width:683px;height:156px;background:var(--footer)}
.col{top:22px;color:var(--footer-text);font-size:7px;line-height:12.3px}
.col h4{font-weight:400;font-size:10px;color:#fff;margin-bottom:12px}
.contact-line{display:flex;align-items:center;gap:8px;color:#fff;margin-top:6px}
.tweet{display:flex;gap:8px}
.tweet .time{color:var(--tweet)}
.signup{display:flex;margin-top:9px}
.signup span{width:84px;height:18px;background:#333;border:1px solid #555;color:#bbb;font-size:7px;padding:4px 8px}
.signup b{width:24px;height:18px;background:var(--tweet);color:#fff;font-weight:400;font-size:7px;text-align:center;line-height:18px}
.bottom-bar{left:0;top:1152px;width:683px;height:48px;background:var(--bottom)}
.copyright{left:81px;top:20px;font-size:7.5px;color:#ccc}
.social{top:17px;display:flex;gap:5px;left:548px}
.social span{width:15px;height:15px;border-radius:50%;background:#8b8b8b}
.social span.first{background:var(--tweet)}
</style>
</head>
<body>

<header class="site-header abs">
  <div class="logo abs"><span class="logo-square"></span>Brightcoat</div>
  <nav class="nav abs">
    <a class="active" style="left:0">HOME</a>
    <a style="left:58px">ABOUT US</a>
    <a style="left:132px">OUR SERVICES</a>
    <a style="left:220px">RESOURCES</a>
    <a style="left:300px">CONTACT US</a>
  </nav>
</header>

<section class="hero abs" role="img" aria-label="Painter in work clothes sealing a red tiled roof beside a brick wall">
  <div class="hero-title abs">At brightcoat painting</div>
  <div class="hero-sub abs">we are focused on quality workmanship<br>We are committed</div>
  <div class="dots abs"><span class="on"></span><span></span><span></span><span></span></div>
</section>

<section class="quality abs">
  <h2 class="section-title abs" style="top:20px">Quality and Service</h2>
  <svg class="divider abs" style="top:44px" viewBox="0 0 163 10"><line x1="0" y1="5" x2="163" y2="5" stroke="#c8c8c8"/><rect x="77" y="1" width="8" height="8" transform="rotate(45 81 5)" fill="#c8c8c8"/></svg>
  <p class="intro abs">Brightcoat Painting Services is a Melbourne family owned Painting &amp; Decorating business based in Ashford, in the south east of Melbourne. We proudly provide domestic and commercial painting services across all suburbs of metropolitan Melbourne.</p>

  <div class="service abs" style="left:75px;top:97px">
    <div class="badge"><svg width="30" height="34" viewBox="0 0 30 34" fill="none" stroke="#fff" stroke-width="1.4"><path d="M15 7a8 8 0 0 0-5 14v4h10v-4a8 8 0 0 0-5-14z"/><line x1="11" y1="28" x2="19" y2="28"/><line x1="12" y1="31" x2="18" y2="31"/><line x1="15" y1="0" x2="15" y2="3"/><line x1="3" y1="6" x2="5" y2="8"/><line x1="27" y1="6" x2="25" y2="8"/><line x1="0" y1="15" x2="3" y2="15"/><line x1="27" y1="15" x2="30" y2="15"/></svg></div>
    <h3>DOMESTIC</h3>
    <p>Brightcoat Painting Services is a Melbourne family owned Painting &amp; Decorating in Ashford, in the south east of</p>
  </div>
  <div class="service abs" style="left:207px;top:97px">
    <div class="badge"><svg width="28" height="32" viewBox="0 0 28 32" fill="none" stroke="#fff" stroke-width="1.5"><rect x="2" y="2" width="20" height="27"/><line x1="6" y1="8" x2="18" y2="8"/><line x1="6" y1="13" x2="18" y2="13"/><line x1="6" y1="18" x2="13" y2="18"/><path d="M14 25l10-10 3 3-10 10h-3z" fill="#fff"/></svg></div>
    <h3>COMMERCIAL</h3>
    <p>Brightcoat Painting Services is a Melbourne family owned Painting &amp; Decorating in Ashford, in the south east of</p>
  </div>
  <div class="service abs" style="left:343px;top:97px">
    <div class="badge"><svg width="48" height="30" viewBox="0 0 48 30" fill="#fff"><circle cx="12" cy="15" r="9"/><circle cx="12" cy="15" r="3.5" fill="#1d6c9e"/><circle cx="30" cy="9" r="5"/><path d="M22 28a8 8 0 0 1 16 0z"/><circle cx="40" cy="10" r="4"/><path d="M34 28a6 7 0 0 1 13 0z"/></svg></div>
    <h3>INDUSTRIAL</h3>
    <p>Brightcoat Painting Services is a Melbourne family owned Painting &amp; Decorating in Ashford, in the south east of</p>
  </div>
  <div class="service abs" style="left:478px;top:97px">
    <div class="badge"><svg width="34" height="32" viewBox="0 0 34 32" fill="#fff"><circle cx="12" cy="12" r="9"/><circle cx="12" cy="12" r="3.5" fill="#1d6c9e"/><circle cx="25" cy="23" r="7"/><circle cx="25" cy="23" r="2.7" fill="#1d6c9e"/></svg></div>
    <h3>HERITAGE</h3>
    <p>Brightcoat Painting Services is a Melbourne family owned Painting &amp; Decorating in Ashford, in the south east of</p>
  </div>
</section>

<section class="gallery abs">
  <h2 class="section-title abs" style="top:10px">Gallery</h2>
  <svg class="divider abs" style="top:32px" viewBox="0 0 163 10"><line x1="0" y1="5" x2="163" y2="5" stroke="#c0c0c0"/><rect x="77" y="1" width="8" height="8" transform="rotate(45 81 5)" fill="#c0c0c0"/></svg>
  <div class="photo abs" style="left:81px;top:53px;background:linear-gradient(90deg,#4a3328,#7a6355 45%,#3d2a20)" role="img" aria-label="Freshly painted interior with timber panelled walls"></div>
  <div class="photo abs" style="left:260px;top:53px;background:linear-gradient(90deg,#4e3428,#8d7a6a 50%,#4a2e24)" role="img" aria-label="Kitchen area with dark timber walls and window"></div>
  <div class="photo abs" style="left:439px;top:53px;background:linear-gradient(180deg,#a89c8c,#ddd6c8 45%,#3a3632 80%,#7a7068)" role="img" aria-label="Ceiling and eaves painting detail"></div>
  <div class="photo abs" style="left:81px;top:159px;background:linear-gradient(90deg,#e6e2dc 15%,#8a4a26 30%,#6e3a1e 65%,#d8d2ca 75%,#7a6e6a)" role="img" aria-label="Varnished timber door in white frame"></div>
  <div class="photo abs" style="left:260px;top:159px;background:linear-gradient(90deg,#d8d4d2 10%,#8a5068 30%,#6e3a54 90%)" role="img" aria-label="Room with freshly painted plum feature wall"></div>
  <div class="photo abs" style="left:439px;top:159px;background:linear-gradient(90deg,#8a4030,#6a3020 25%,#3a2418 50%,#6a3020 75%,#8a4030)" role="img" aria-label="Stained timber entry doors set in brick"></div>
</section>

<section class="partners abs" aria-label="Partner brands">
  <div class="partner abs" role="img" aria-label="Workmanship warranty badge" style="left:101px;top:26px;background:#1d4f8a"></div>
  <div class="partner abs" role="img" aria-label="nearbyfind listing badge" style="left:192px;top:26px;background:#1fa0dc"></div>
  <div class="partner abs" role="img" aria-label="Corvale Paints badge" style="left:297px;top:26px;background:#1a2d6a"></div>
  <div class="partner abs" role="img" aria-label="Harlow Coatings badge" style="left:400px;top:26px;background:#e0522a"></div>
  <div class="partner abs" role="img" aria-label="Pellmont Paint badge" style="left:522px;top:26px;background:#c2283a"></div>
</section>

<footer class="site-footer abs">
  <div class="col abs" style="left:81px;width:112px">
    <h4>TESTIMONIAL</h4>
    "Rob lives up to the name 'Brightcoat Painter'.<br>men in and out of the house during the Reno he stood out as of our churches and again work in our parish school.rates and the highest recommendation. Thanks Rob."
  </div>
  <div class="col abs" style="left:214px;width:118px">
    <h4>CONTACT</h4>
    Lorem Ipsum is simply dummy text of the printing and typesetting
    <div class="contact-line" style="margin-top:10px"><svg width="8" height="10" viewBox="0 0 8 10"><path d="M4 0a4 4 0 0 1 4 4c0 3-4 6-4 6S0 7 0 4a4 4 0 0 1 4-4z" fill="#7ab4dc"/><circle cx="4" cy="4" r="1.4" fill="#4a4a4a"/></svg>Ashford, Victoria 3999, Australia</div>
    <div class="contact-line"><svg width="9" height="7" viewBox="0 0 9 7"><rect width="9" height="7" fill="#7ab4dc"/><path d="M0 0l4.5 4L9 0" stroke="#4a4a4a" fill="none"/></svg>info@brightcoatpainting.com</div>
    <div class="contact-line"><svg width="8" height="8" viewBox="0 0 8 8"><path d="M1 0h2l1 2-1.2 1a5 5 0 0 0 2.2 2.2L6 4l2 1v2a1 1 0 0 1-1 1A7 7 0 0 1 0 1a1 1 0 0 1 1-1z" fill="#7ab4dc"/></svg>1300 555 014</div>
  </div>
  <div class="col abs" style="left:344px;width:132px">
    <h4>LATEST TWEETS</h4>
    <div class="tweet"><svg width="9" height="8" viewBox="0 0 9 8" style="margin-top:3px;flex:none"><path d="M0 6l4-1 5-5-1 5-4 3z" fill="#5fa8d6"/></svg><div>Lorem Ipsum is simply dummy text of the printing and typesetting industry. Lorem Ipsum<br><span class="time">1 Hour Ago</span></div></div>
    <div class="tweet" style="margin-top:11px"><svg width="9" height="8" viewBox="0 0 9 8" style="margin-top:3px;flex:none"><path d="M0 6l4-1 5-5-1 5-4 3z" fill="#5fa8d6"/></svg><div>Lorem Ipsum is simply dummy text of the printing and typeset-<br><span class="time">1 Hour Ago</span></div></div>
  </div>
  <div class="col abs" style="left:496px;width:110px">
    <h4>NEWS LETTER</h4>
    <span style="line-height:10.5px;display:block">Type your email address below and recive our daily news letter for free</span>
    <div class="signup"><span>Email Address</span><b>GO</b></div>
  </div>
</footer>

<div class="bottom-bar abs">
  <div class="copyright abs">Copyright 2014 © Brightcoat Painting . All rights reserved</div>
  <div class="social abs" aria-label="Social links"><span class="first"></span><span></span><span></span></div>
</div>

</body>
</html>
```